Business Recognition Design

We need a design for a recognition to be given to business leaders in our community.
The recognition shall be made on a brass plaque on wood panel background (picture attached, please use it as a background), and all drawing must be in vectors and only one color (black).
It should also have a logo on the top and signature on the right bottom.
The text is enclosed in DOC file.
Updates

Reason: just to be able to find the best solution

Reason: None of the suggestion is good enough. Logo in general is too big in comparison with the rest of the plate.

Industry/Entity Type

Business

Requirements
Must have
• - standard Windows font (or possibility to install the same font on Windows), as the name on the recognition shall be printed in the same font
Nice to have
• - some graphic element (in curves) representing achievements in business
- should look great :)

```html
<!DOCTYPE html>
<html lang="en">
<head>
<meta charset="UTF-8">
<title>Recognition Plaque – The Best Entrepreneur in 2013</title>
<link rel="stylesheet" href="https://fonts.googleapis.com/css2?family=Arimo:wght@400;700&display=swap">
<style>
  :root {
    --wood-dark: #3f2414;
    --wood-mid: #6b4028;
    --wood-light: #8a5a3b;
    --brass-deep: #c9a227;
    --brass-mid: #e2c04a;
    --brass-light: #f3dc78;
    --brass-edge: #b58e1c;
    --ink: #151310;
    --emblem-tone: rgba(21, 19, 16, 0.22);
    --emblem-fade: rgba(21, 19, 16, 0);
    --screw-dark: #7a5a10;
    --screw-light: #f1d67a;
  }

  * { box-sizing: border-box; margin: 0; padding: 0; }

  html, body {
    width: 1200px;
    height: 924px;
    overflow: hidden;
    background: #ffffff;
  }

  .plaque {
    position: relative;
    width: 1200px;
    height: 924px;
    background:
      repeating-linear-gradient(90deg, rgba(0,0,0,0.06) 0 3px, transparent 3px 9px),
      linear-gradient(180deg, var(--wood-light), var(--wood-mid) 40%, var(--wood-dark));
    font-family: "Arimo", Arial, sans-serif;
    color: var(--ink);
  }

  .plaque__bevel {
    position: absolute;
    inset: 28px 26px 30px 26px;
    border: 2px solid rgba(0,0,0,0.35);
    box-shadow: inset 0 0 0 2px rgba(255,255,255,0.08);
  }

  .brass-plate {
    position: absolute;
    left: 50px;
    top: 46px;
    width: 1100px;
    height: 834px;
    background:
      repeating-linear-gradient(180deg, rgba(255,255,255,0.10) 0 1px, transparent 1px 3px, rgba(120,80,0,0.06) 3px 4px, transparent 4px 6px),
      linear-gradient(100deg, var(--brass-deep) 0%, var(--brass-mid) 30%, var(--brass-light) 55%, var(--brass-mid) 75%, var(--brass-deep) 100%);
    box-shadow: 0 0 0 2px var(--brass-edge), 0 3px 6px rgba(0,0,0,0.45);
  }

  .screw {
    position: absolute;
    width: 28px;
    height: 28px;
    border-radius: 50%;
    background: radial-gradient(circle at 38% 35%, var(--screw-light), var(--brass-mid) 45%, var(--screw-dark) 100%);
    box-shadow: 0 1px 2px rgba(0,0,0,0.5);
  }
  .screw--tl { left: 79px;  top: 70px; }
  .screw--tr { left: 1107px; top: 70px; }
  .screw--bl { left: 79px;  top: 818px; }
  .screw--br { left: 1107px; top: 818px; }

  .achievement-emblem {
    position: absolute;
    left: 100px;
    top: 88px;
    width: 1030px;
    height: 176px;
    border-radius: 50%;
    background: radial-gradient(closest-side at 53% 50%, var(--emblem-tone), var(--emblem-fade));
  }

  .inscription {
    position: absolute;
    left: 14px;
    width: 100%;
    text-align: center;
    white-space: nowrap;
  }

  .inscription__title {
    top: 317px;
    font-size: 64px;
    font-weight: 400;
    letter-spacing: 2px;
  }
  .inscription__award {
    top: 406px;
    font-size: 38px;
    font-weight: 700;
  }
  .inscription__to {
    top: 470px;
    font-size: 26px;
  }
  .inscription__recipient {
    top: 512px;
    font-size: 38px;
    font-weight: 700;
  }
  .inscription__citation {
    top: 571px;
    font-size: 23px;
    line-height: 40px;
  }
  .inscription__citation strong { font-weight: 700; }

  .plaque__date,
  .plaque__signatory {
    position: absolute;
    top: 767px;
    font-size: 31px;
  }
  .plaque__date { left: 258px; }
  .plaque__date sup { font-size: 18px; vertical-align: 13px; }
  .plaque__signatory { left: 822px; }
</style>
</head>
<body>
  <main class="plaque">
    <div class="plaque__bevel"></div>
    <div class="brass-plate"></div>

    <span class="screw screw--tl"></span>
    <span class="screw screw--tr"></span>
    <span class="screw screw--bl"></span>
    <span class="screw screw--br"></span>

    <div class="achievement-emblem" role="img" aria-label="Black emblem of shooting stars trailing sweeping curved lines, symbolising business achievement"></div>

    <h1 class="inscription inscription__title">RECOGNITION</h1>
    <p class="inscription inscription__award">The Best Entrepreneur in 2013</p>
    <p class="inscription inscription__to">to</p>
    <p class="inscription inscription__recipient">Mr. Daniel R. Whitford,&nbsp; MBA</p>
    <p class="inscription inscription__citation">
      Under the leadership of <strong>Mr. Daniel R. Whitford, MBA</strong><br>
      the company <strong>DR-Whitford Ltd</strong> has been selected<br>
      by a City Council as the best company of The City.
    </p>

    <p class="plaque__date">4<sup>th</sup> July, 2013</p>
    <p class="plaque__signatory">City Mayor</p>
  </main>
</body>
</html>
```